Business cards and stationary design

We just completed the design of our new logo and we need to print new business cards and letterhead for our nonprofit. We are looking for a fresh new design that shows off our new logo. On letterhead, we must have a column on the right or left to include our Board of Directors (up to 45 names) (see attachment)

Industry/Entity Type

Non-Profit

Contact Information for Business Card

Standard business card with name, title, Company name, mailing address phone numbers, email address and website. Tagline on back "Bringing the homeless home"

Font styles to use
Sans Serif

Requirements
Must have
• include pertinent information above
• new logo
• fonts compatible with logo
• should use logo colors only
Nice to have
• tag lines

```html
<!DOCTYPE html>
<html lang="en">
<head>
<meta charset="utf-8">
<title>Harbor Home Alliance – Business Card</title>
<link href="https://fonts.googleapis.com/css2?family=Work+Sans:wght@400;500;600&display=swap" rel="stylesheet">
<style>
  :root {
    --backdrop: #151515;
    --card-white: #ffffff;
    --teal: #0782a0;
    --teal-dark: #0a7c98;
    --gold: #f6b221;
    --ink: #333333;
    --white: #ffffff;
  }
  * { margin: 0; padding: 0; box-sizing: border-box; }
  html, body {
    width: 1200px; height: 897px; overflow: hidden;
    background: var(--backdrop);
    font-family: "Work Sans", Arial, sans-serif;
  }
  .stage { position: relative; width: 1200px; height: 897px; }

  .card {
    position: absolute; left: 303px; width: 594px; height: 339px; overflow: hidden;
  }
  .card-front { top: 92px; background: var(--card-white); }
  .card-back  { top: 469px; background: var(--teal); }

  .brand-name {
    position: absolute; white-space: nowrap; font-weight: 600;
    letter-spacing: 3px; text-transform: uppercase;
  }
  .card-front .brand-name {
    left: 56px; top: 190px; font-size: 18px; color: var(--teal);
  }
  .brand-mark {
    position: absolute; width: 16px; height: 16px; border-radius: 50%;
  }
  .card-front .brand-mark { left: 176px; top: 160px; background: var(--gold); }

  .contact-block { position: absolute; left: 379px; top: 103px; }
  .person-name {
    font-size: 22px; font-weight: 500; color: var(--teal); line-height: 1.1;
    text-transform: uppercase;
  }
  .person-title { font-size: 15px; color: var(--ink); margin-top: 2px; }
  .divider { width: 160px; height: 1.5px; background: var(--teal); margin: 17px 0 14px; }
  .contact-list { list-style: none; font-size: 15px; color: var(--ink); line-height: 18.5px; }
  .contact-list li { display: flex; align-items: center; gap: 8px; }
  .contact-list svg { width: 9px; height: 9px; flex: none; }

  .footer-band { position: absolute; left: 0; top: 0; width: 594px; height: 339px; }
  .mailing-address {
    position: absolute; left: 0; right: 0; top: 307px; text-align: center;
    font-size: 14.5px; color: var(--white); letter-spacing: 0.3px;
  }

  .card-back .brand-name {
    left: 0; right: 0; top: 155px; text-align: center;
    font-size: 24px; color: var(--white); letter-spacing: 4px;
  }
  .card-back .brand-mark { left: 289px; top: 122px; background: var(--white); }
</style>
</head>
<body>
<main class="stage">
  <section class="card card-front">
    <span class="brand-mark"></span>
    <div class="brand-name">Harbor Home Alliance</div>

    <div class="contact-block">
      <div class="person-name">Jordan Avery</div>
      <div class="person-title">Director</div>
      <div class="divider"></div>
      <ul class="contact-list">
        <li>
          <svg viewBox="0 0 10 10"><path d="M2 0.5 L4 2.8 L3 4 Q4.3 6 6 7 L7.2 6 L9.5 8 L8 9.5 Q3 9 0.5 2 Z" fill="var(--teal)"/></svg>
          555,010.2417
        </li>
        <li>
          <svg viewBox="0 0 10 10"><rect x="0.7" y="2" width="8.6" height="6" fill="none" stroke="var(--teal)" stroke-width="1.2"/><path d="M0.7 2 L5 5.5 L9.3 2" fill="none" stroke="var(--teal)" stroke-width="1.2"/></svg>
          info@harborhome.org
        </li>
        <li>
          <svg viewBox="0 0 10 10"><circle cx="5" cy="5" r="4.3" fill="none" stroke="var(--teal)" stroke-width="1"/><ellipse cx="5" cy="5" rx="1.8" ry="4.3" fill="none" stroke="var(--teal)" stroke-width="0.9"/><path d="M0.7 5 H9.3" stroke="var(--teal)" stroke-width="0.9"/></svg>
          www.harborhome.org
        </li>
      </ul>
    </div>

    <svg class="footer-band" viewBox="0 0 594 339" aria-hidden="true">
      <path d="M0 324 Q297 230 594 324" fill="none" stroke="var(--gold)" stroke-width="3.5"/>
      <path d="M0 330 Q297 236 594 330 L594 339 L0 339 Z" fill="var(--teal-dark)"/>
    </svg>
    <div class="mailing-address">P.O. Box 402918, Maple Falls, Texas 75999</div>
  </section>

  <section class="card card-back">
    <span class="brand-mark"></span>
    <div class="brand-name">Harbor Home Alliance</div>
  </section>
</main>
</body>
</html>
```